Verodex business card

Business card for sustainable investment company called "Verodex". Verodex is an exchange platform selling carbon credits between buyers and sellers. Carbon Credits are an environmental commodity for reducing global carbon emissions.

the card should obviously have our logo and the theme should be sustainability/environment mixed with a trading platform.

Contact Information for Business Card

Logo, Name, Title, Phone, Email

Colors
0054AA
0677BA
7BADD7
CADEEF
E8F1F8
0094D4
00A9DD
6FCCEA
C7EBF8
E9F6FB
00AB8E
00BBA5
67D7C9
C6EFE9
E9F9F6
59FF00
82FF00
B8FF75
E3FFCB
F4FFEA

```html
<!DOCTYPE html>
<html lang="en">
<head>
<meta charset="utf-8">
<title>Verodex business card</title>
<link rel="stylesheet" href="https://fonts.googleapis.com/css2?family=Montserrat:wght@700&family=Open+Sans:wght@400;700&display=swap">
<style>
  :root {
    --stage: #16171a;
    --card: #232226;
    --ink: #ffffff;
    --accent: #4a8fd4;
    --accent-light: #6fcce0;
    --rule: #8a8a90;
  }
  * { box-sizing: border-box; margin: 0; padding: 0; }
  html, body { width: 1200px; height: 780px; overflow: hidden; }
  body {
    background: var(--stage);
    display: flex;
    align-items: center;
    justify-content: center;
    gap: 40px;
    font-family: "Open Sans", Arial, sans-serif;
  }
  .card {
    width: 560px;
    height: 320px;
    background: var(--card);
    border-radius: 4px;
    position: relative;
    overflow: hidden;
  }

  /* Contact side */
  .card--contact { display: flex; align-items: center; }
  .brand-block {
    width: 250px;
    display: flex;
    align-items: center;
    justify-content: center;
    gap: 12px;
  }
  .brand-block__square {
    width: 22px; height: 22px;
    background: var(--accent);
  }
  .brand-block__name {
    font-family: "Open Sans", Arial, sans-serif;
    font-weight: 700;
    font-size: 34px;
    color: var(--accent);
  }
  .divider {
    width: 1px;
    height: 200px;
    background: var(--rule);
  }
  .contact {
    padding-left: 34px;
    color: var(--ink);
  }
  .contact__name {
    font-weight: 700;
    font-size: 27px;
    line-height: 1.1;
    color: var(--accent);
  }
  .contact__title {
    font-size: 16px;
    margin-bottom: 8px;
  }
  .contact__address {
    font-size: 15px;
    line-height: 1.35;
    font-style: normal;
    margin-bottom: 4px;
  }
  .contact__list { list-style: none; font-size: 15px; line-height: 1.4; }
  .contact__list li { display: flex; align-items: center; gap: 8px; }
  .contact__icon { width: 13px; height: 13px; flex: none; }

  /* Brand side */
  .card--brand {
    display: flex;
    align-items: center;
    justify-content: center;
    gap: 16px;
  }
  .wordmark__square {
    width: 26px; height: 26px;
    background: var(--accent);
  }
  .wordmark {
    font-family: "Montserrat", Arial, sans-serif;
    font-weight: 700;
    font-size: 54px;
    letter-spacing: 1px;
    text-transform: uppercase;
    color: var(--ink);
  }
</style>
</head>
<body>

  <section class="card card--contact" aria-label="Business card, contact side">
    <div class="brand-block">
      <span class="brand-block__square"></span>
      <span class="brand-block__name">Verodex</span>
    </div>
    <div class="divider"></div>
    <div class="contact">
      <p class="contact__name">Marta Kovalenko</p>
      <p class="contact__title">Managing Director</p>
      <address class="contact__address">4180 Linden Ave. Suite 310<br>Oakvale, TX 75090</address>
      <ul class="contact__list">
        <li>
          <svg class="contact__icon" viewBox="0 0 16 16" aria-hidden="true"><path fill="#4a8fd4" d="M3.6 1.2 6 3.6 4.6 5.4c.9 2 2.5 3.6 4.4 4.5l1.6-1.4 2.4 2.4-1.6 2.4C6.7 13 3 9.3 1.2 4.6z"/></svg>
          (555) 214-6083
        </li>
        <li>
          <svg class="contact__icon" viewBox="0 0 16 16" aria-hidden="true"><rect x="1" y="3" width="14" height="10" fill="#4a8fd4"/><path d="M1.5 3.5 8 9l6.5-5.5" fill="none" stroke="#232226" stroke-width="1.3"/></svg>
          hello@verodex.com
        </li>
        <li>
          <svg class="contact__icon" viewBox="0 0 16 16" aria-hidden="true"><circle cx="8" cy="8" r="6.5" fill="none" stroke="#4a8fd4" stroke-width="1.5"/><path d="M1.5 8h13M8 1.5c-3 3.5-3 9.5 0 13M8 1.5c3 3.5 3 9.5 0 13" fill="none" stroke="#4a8fd4" stroke-width="1.1"/></svg>
          www.verodex.com
        </li>
      </ul>
    </div>
  </section>

  <section class="card card--brand" aria-label="Business card, brand side">
    <span class="wordmark__square"></span>
    <span class="wordmark">Verodex</span>
  </section>

</body>
</html>
```